We need a new business card that reflects who we are. Professional, classy, modern, and service ori

We need a business card design for a window coverings design company in Kansas City called Bright Lane Interiors. We offer professional, modern, and high quality window covering products. We are looking to portray an image of a big, national franchise. We are a 5 location (with showrooms) business with 10 professional designers and 4 professional installers. These cards will be used with Thank you cards, given to realtors, and asked for referrals with.

Target Market(s)

Kansas City

Industry/Entity Type

Business

Contact Information for Business Card

We would like our card to look clean and simple on the front, featuring our logo and Marlow Fenwick's. Our designers' phone numbers and emails should be displayed as well as their title.

Font styles to use
Sans Serif

Colors

Designer to choose colors to be used in the design.

Requirements
Must have
• Front - Logos, name, phone number, email address
• Back - Showroom locations, social media? Appt date/time?
Nice to have
• I would like a clean and modern look (not contemporary. I like a white background, but I am open to ideas. Looking for a "National chain" look for a small business.
Should not have
• Too much busyness.

```html
<!DOCTYPE html>
<html lang="en">
<head>
<meta charset="utf-8">
<title>Bright Lane Interiors – Business Card</title>
<link rel="stylesheet" href="https://fonts.googleapis.com/css2?family=Roboto:wght@400;500;700&display=swap">
<style>
  :root {
    --backdrop: #e8e5e0;
    --card-dark: #000000;
    --card-light: #f4f4f3;
    --brand-red: #c9363e;
    --ink-white: #ffffff;
    --ink-grey: #5a5a5a;
    --ink-dark: #222222;
    --leader: #8a8a8a;
    --partner-accent: #f39b2b;
  }
  * { margin: 0; padding: 0; box-sizing: border-box; }
  html, body {
    width: 1200px; height: 960px; overflow: hidden;
    background: var(--backdrop);
    font-family: "Roboto", Arial, sans-serif;
  }
  .canvas { position: relative; width: 1200px; height: 960px; }
  .card {
    position: absolute; width: 600px; height: 342px;
    box-shadow: 0 2px 6px rgba(0,0,0,0.25);
  }

  /* Front */
  .card-front { left: 322px; top: 109px; background: var(--card-dark); text-align: center; }
  .contact { position: absolute; left: 0; right: 0; top: 107px; }
  .contact-name { color: var(--brand-red); font-size: 23px; font-weight: 500; line-height: 28px; }
  .contact-title { color: var(--ink-white); font-size: 16px; font-weight: 500; line-height: 20px; }
  .contact-phone { color: var(--ink-white); font-size: 20px; line-height: 26px; }
  .contact-links { width: 200px; margin: 0 auto; }
  .contact-link {
    display: block; color: var(--ink-white); font-size: 14px; line-height: 17px;
    padding: 0 0 3px; border-bottom: 1px solid var(--brand-red);
  }
  .contact-link + .contact-link { padding-top: 4px; }

  /* Back */
  .card-back { left: 320px; top: 493px; background: var(--card-light); }
  .brand { position: absolute; left: 72px; top: 62px; width: 230px; text-align: center; }
  .brand-mark { display: block; width: 48px; height: 48px; margin: 0 auto 18px; background: var(--brand-red); border-radius: 50%; }
  .brand-name { color: var(--ink-dark); font-size: 21px; font-weight: 400; line-height: 26px; }
  .brand-tagline { color: var(--ink-dark); font-size: 11px; line-height: 14px; margin-top: 6px; }

  .showrooms { position: absolute; left: 340px; top: 40px; }
  .showrooms-heading { color: var(--brand-red); font-size: 14px; font-weight: 700; line-height: 18px; }
  .showrooms-list { list-style: none; }
  .showrooms-list li { color: var(--ink-grey); font-size: 14.5px; font-weight: 500; line-height: 18px; }
  .partner { display: flex; align-items: center; gap: 5px; margin-top: 8px; color: var(--ink-grey); font-size: 12px; font-weight: 500; }
  .partner-dot { width: 14px; height: 14px; border-radius: 50%; background: var(--partner-accent); }
  .social { display: flex; gap: 3px; margin-top: 9px; }
  .social-dot { width: 17px; height: 17px; border-radius: 50%; background: var(--brand-red); }

  .appointment { position: absolute; left: 43px; right: 58px; color: var(--brand-red); font-size: 16px; display: flex; align-items: baseline; }
  .appointment-name { top: 234px; }
  .appointment-when { top: 275px; }
  .leader { flex: 1; border-bottom: 1px dotted var(--leader); margin: 0 4px 0 6px; height: 1px; }
  .leader-short { flex: 0 0 213px; }
  .leader-time { flex: 0 0 133px; }
  .ampm { font-size: 12px; margin-left: 2px; }
</style>
</head>
<body>
<main class="canvas">
  <section class="card card-front" aria-label="Card front">
    <div class="contact">
      <p class="contact-name">JORDAN AVERY</p>
      <p class="contact-title">DESIGNER</p>
      <p class="contact-phone">913.555.0148</p>
      <div class="contact-links">
        <span class="contact-link">info@brightlaneinteriors.com</span>
        <span class="contact-link">www.brightlaneinteriors.com</span>
      </div>
    </div>
  </section>

  <section class="card card-back" aria-label="Card back">
    <div class="brand">
      <span class="brand-mark"></span>
      <p class="brand-name">Bright Lane Interiors</p>
      <p class="brand-tagline">Blinds, Shades, Shutters, Draperies &amp; Decor</p>
    </div>

    <div class="showrooms">
      <p class="showrooms-heading">SHOWROOM LOCATIONS</p>
      <ul class="showrooms-list">
        <li>MAPLE RIDGE</li>
        <li>CEDAR HILLS</li>
        <li>WILLOW BEND</li>
        <li>NORTH POINT</li>
        <li>OAK HARBOR</li>
      </ul>
      <div class="partner"><span>Marlow Fenwick Gallery</span><span class="partner-dot"></span></div>
      <div class="social" aria-label="Social media">
        <span class="social-dot"></span><span class="social-dot"></span><span class="social-dot"></span><span class="social-dot"></span>
      </div>
    </div>

    <div class="appointment appointment-name">Name :<span class="leader"></span></div>
    <div class="appointment appointment-when">Date :<span class="leader leader-short"></span>Time :<span class="leader leader-time"></span><span class="ampm">AM/PM</span></div>
  </section>
</main>
</body>
</html>
```